Investor Slide Deck

Simple idea - take a model investor deck and build out a investor deck for K7V. I will complete the data, I need a template to work from within. I will attach a model investor deck and a blank K7V that I need built out to K7V. Use the K7V Pwrpt to build out the investor deck

```html
<!DOCTYPE html>
<html lang="en">
<head>
<meta charset="utf-8">
<title>K7V Investor Deck 2024</title>
<link href="https://fonts.googleapis.com/css2?family=Quicksand:wght@400;500;600;700&display=swap" rel="stylesheet">
<style>
:root{
  --canvas:#eef0f1;
  --navy:#0b3640;
  --magenta:#b0125b;
  --orange:#ff5a0a;
  --teal:#1b6c82;
  --yellow:#f6c12a;
  --ink:#1a1a1a;
  --muted:#8a8f93;
  --card-line:#dcdfe2;
}
*{box-sizing:border-box;margin:0;padding:0}
html,body{width:1037px;height:1200px;overflow:hidden;background:var(--canvas);font-family:"Quicksand",sans-serif;color:var(--ink)}
.deck{position:relative;width:1037px;height:1200px}
.slide{position:absolute;width:485px;height:273px;background:#fff;overflow:hidden}
.abs{position:absolute}
.slide-title{position:absolute;left:11px;top:4px;font-size:20px;font-weight:700;color:var(--ink);letter-spacing:.2px}
.brand-mark{position:absolute;right:13px;top:10px;font-size:19px;font-weight:700;color:var(--magenta);line-height:1}
.footer{position:absolute;left:13px;right:13px;top:241px;height:25px;border-radius:13px;background:var(--magenta);color:#fff;display:flex;align-items:center;justify-content:space-between;padding:0 9px 0 12px;font-size:7px;font-weight:700}
.footer .name{letter-spacing:.3px}
.footer .name b{font-size:10px;margin-right:3px}
.photo{position:absolute}
.tiny{font-size:4.3px;line-height:1.6;color:var(--muted)}
.h9{font-size:9.5px;font-weight:600;color:var(--navy);line-height:1.25}
/* cover */
.cover{background:var(--navy)}
.cover .big-mark{position:absolute;left:60px;top:60px;font-size:66px;font-weight:700;color:var(--orange);line-height:1}
.cover .deck-label{position:absolute;left:40px;top:171px;font-size:18px;font-weight:600;color:#fff}
/* problems */
.intro{position:absolute;left:121px;top:8px;width:300px;font-size:6.5px;line-height:1.55;color:#777}
.problem .h9{width:95px}
.problem .tiny{width:90px;margin-top:3px}
/* bullets */
.sol{position:absolute;width:136px}
.sol .h9{position:relative;padding-left:10px}
.sol .h9::before{content:"";position:absolute;left:0;top:3px;width:5px;height:5px;border-radius:50%;background:var(--magenta)}
.sol .tiny{padding-left:10px;margin-top:4px}
/* cards */
.card{position:absolute;width:139px;height:191px;border:1px solid var(--card-line);border-radius:4px;background:#fff}
.card .photo{left:5px;width:127px;height:93px;border-radius:4px}
.card .h9{position:absolute;left:9px;width:124px}
.card ul{position:absolute;left:9px;width:124px;list-style:none}
.card li{position:relative;padding-left:9px;font-size:4.6px;line-height:1.95;color:#555}
.card li::before{content:"›";position:absolute;left:0;top:-1px;font-size:7px;font-weight:700;color:var(--magenta)}
/* traction */
.chart-title{position:absolute;left:45px;top:42px;width:130px;text-align:center;font-size:12px;font-weight:600;line-height:1.25}
.stat{position:absolute;width:101px;height:86px;border:1px solid #eceef0;border-radius:4px;padding:5px 8px}
.stat .num{font-size:17px;font-weight:600;line-height:1.1}
.stat .lbl{font-size:6.8px;line-height:1.35;margin-top:3px}
.stat .lbl em{font-style:normal;color:var(--magenta)}
.stat .desc{font-size:5.4px;line-height:1.6;color:#555;margin-top:5px}
/* roadmap */
.step-no{position:absolute;width:42px;height:42px;border-radius:50%;background:#efc6d8;display:flex;align-items:center;justify-content:center}
.step-no span{width:32px;height:32px;border-radius:50%;background:var(--magenta);color:#fff;font-size:15px;font-weight:600;display:flex;align-items:center;justify-content:center}
.step{position:absolute;left:277px;width:190px}
.step h3{font-size:11px;font-weight:600;line-height:1.35}
.step ul{list-style:none;margin-top:5px}
.step li{position:relative;padding-left:10px;font-size:6px;line-height:1.75;color:#666}
.step li::before{content:"";position:absolute;left:0;top:3px;width:3.5px;height:3.5px;border-radius:50%;background:var(--teal)}
</style>
</head>
<body>
<div class="deck">

<!-- 01 Cover -->
<section class="slide cover" style="left:19px;top:18px">
  <div class="big-mark">K7V</div>
  <div class="deck-label">Investor Deck, 2024</div>
  <svg class="abs" style="left:0;top:0" width="485" height="273" viewBox="0 0 485 273">
    <path d="M348 15 A109 109 0 0 0 289 216" fill="none" stroke="var(--yellow)" stroke-width="2.5"/>
    <path d="M300 225 A109 109 0 0 0 348 15" fill="none" stroke="var(--magenta)" stroke-width="2.5" transform="rotate(180 348 124)"/>
  </svg>
  <div class="photo" role="img" aria-label="Engineer in safety vest holding a clipboard beside rows of solar panels" style="left:250px;top:26px;width:196px;height:196px;border-radius:50%;background:linear-gradient(160deg,#c9d4dc 0%,#6f8494 45%,#7b6a4c 100%)"></div>
  <div class="footer"><span class="name"><b>K7V</b>KESTREL SEVEN VOLT</span><span>Page No:01</span></div>
</section>

<!-- 02 Problems -->
<section class="slide" style="left:519px;top:18px">
  <div class="slide-title">Problems</div>
  <p class="intro">Every year, the rise in prices of electricity is burning a hole in the pocket of consumers. Solar Power is a reliable solution, but the industry is facing its own set of challenges.</p>
  <div class="brand-mark">K7V</div>
  <svg class="abs" style="left:0;top:0" width="485" height="240" viewBox="0 0 485 240">
    <defs>
      <g id="ring">
        <path d="M0 -21 A21 21 0 0 0 0 21" fill="none" stroke="var(--yellow)" stroke-width="2.4"/>
        <path d="M0 21 A21 21 0 0 0 0 -21" fill="none" stroke="var(--magenta)" stroke-width="2.4"/>
        <circle r="15.5" fill="#fff" stroke="#e9e9e9" stroke-width="1"/>
        <circle r="6" fill="none" stroke="#333" stroke-width="1"/>
      </g>
    </defs>
    <use href="#ring" x="35" y="80"/>
    <use href="#ring" x="185" y="80"/>
    <use href="#ring" x="336" y="124"/>
    <use href="#ring" x="35" y="177"/>
    <use href="#ring" x="185" y="177"/>
  </svg>
  <div class="abs problem" style="left:63px;top:56px"><div class="h9">Poor<br>Quality Components</div><p class="tiny">The use of low-quality solar panels and components in solar plant construction is impacting their efficiency and lifespan.</p></div>
  <div class="abs problem" style="left:212px;top:56px"><div class="h9">Poor<br>Installation</div><p class="tiny">Solar plant installations demand precision; poor installation can lead to downtime, damage, and efficiency loss.</p></div>
  <div class="abs problem" style="left:364px;top:99px"><div class="h9" style="width:112px">Lack of Transparency in Pricing and Performance</div><p class="tiny" style="width:105px">Customers might encounter unexpected hidden costs during installation and lower energy generation than initially agreed upon.</p></div>
  <div class="abs problem" style="left:63px;top:152px"><div class="h9">Lack of<br>Awareness</div><p class="tiny">Limited awareness of government subsidies and inadequate financing options for high-cost solar plant purchases can lead to missed product benefits.</p></div>
  <div class="abs problem" style="left:212px;top:152px"><div class="h9" style="width:110px">Unreliable Customer and Warranty Support</div><p class="tiny" style="width:100px">Challenges in reaching timely support and clarifying warranty terms can result in customer frustration and self-reliance for issue resolution.</p></div>
  <div class="footer"><span class="name"><b>K7V</b>KESTREL SEVEN VOLT</span><span>Page No:02</span></div>
</section>

<!-- 03 Solutions -->
<section class="slide" style="left:19px;top:308px">
  <div class="slide-title">Solutions</div>
  <div class="brand-mark">K7V</div>
  <div class="photo" role="img" aria-label="Solar farm with wind turbines under a blue sky" style="left:10px;top:35px;width:151px;height:192px;border-radius:22px;background:linear-gradient(180deg,#7fa9d1 0%,#c8dceb 50%,#7e8f64 78%,#4f5d3a 100%)"></div>
  <div class="sol" style="left:182px;top:42px"><div class="h9">Quality Components</div><p class="tiny">With a portfolio of 2500+ solar power plants, we excel in selecting technically compatible, premium components to guarantee long-term results, planning an automated facility for high-quality solar panels.</p></div>
  <div class="sol" style="left:182px;top:99px"><div class="h9">Awareness About Subsidies And Financing</div><p class="tiny">Company Name Energy educates residential consumers about Central Government subsidies and collaborates with banks and NBFCs to facilitate solar financing for various client segments.</p></div>
  <div class="sol" style="left:182px;top:164px"><div class="h9">Dedicated Customer And Warranty Support</div><p class="tiny">Company Name Energy's dedicated team offers comprehensive after-sales support, facilitating swift warranty-covered service at local offices for our Panels and Inverters, eliminating brand-related delays.</p></div>
  <div class="sol" style="left:339px;top:72px"><div class="h9">Efficient Installation</div><p class="tiny">Our proficient design and site engineers create solar plants to precise technical specs, ensuring low-maintenance installations with a flawless track record of zero system failures.</p></div>
  <div class="sol" style="left:339px;top:137px"><div class="h9">Transparent Pricing &amp; Performance</div><p class="tiny">We ensure transparent pricing and performance commitments in our projects. Our designs are created with the shadow analysis of solar panels for optimum result. We also provide the projected power generation and payback report of solar plant using software.</p></div>
  <div class="footer"><span class="name"><b>K7V</b>KESTREL SEVEN VOLT</span><span>Page No:03</span></div>
</section>

<!-- 04 Products -->
<section class="slide" style="left:519px;top:308px">
  <div class="slide-title">Our Products</div>
  <div class="brand-mark">K7V</div>
  <div class="card" style="left:16px;top:41px">
    <div class="photo" role="img" aria-label="Parent and child playing beside bifacial solar panels" style="top:4px;background:linear-gradient(180deg,#8fb6d8 0%,#35506b 55%,#7c8f4a 100%)"></div>
    <div class="h9" style="top:103px">Bi-facial Solar PV Module</div>
    <ul style="top:121px"><li>High Module Efficiency</li><li>Positive Power Tolerance upto 5 Watt</li><li>100% EL + VI Testing with 3 Stages</li><li>Increased Shade Tolerance</li><li>Split Junction Box Improves Heat Dissipation</li></ul>
  </div>
  <div class="card" style="left:173px;top:41px">
    <div class="photo" role="img" aria-label="Rows of grid tie inverter cabinets at a solar site" style="top:4px;background:linear-gradient(180deg,#3f6f86 0%,#1f4a5e 55%,#6e7a73 100%)"></div>
    <div class="h9" style="top:103px">Single Phase Grid Tie Inverters</div>
    <ul style="top:127px"><li>High AC/DC Ratio for Higher Yields</li><li>Compact and Lightweight for easy installation.</li><li>User Friendly Web and App based monitoring.</li><li>Multiple MPPT Design With IDA Technology (Intelligent Disturbance Algorithm)</li></ul>
  </div>
  <div class="card" style="left:329px;top:41px">
    <div class="photo" role="img" aria-label="Technician in hard hat inspecting a wall-mounted inverter" style="top:4px;background:linear-gradient(180deg,#8c949a 0%,#5d6a72 50%,#c9c9c2 100%)"></div>
    <div class="h9" style="top:103px">Three Phase Grid Tie Inverters</div>
    <ul style="top:127px"><li>Efficiency Upto 98.9%</li><li>Frequency Drop Control Technology</li><li>User Friendly Web and App based monitoring.</li><li>Weather, Consumption, String Level Monitoring System.</li></ul>
  </div>
  <div class="footer"><span class="name"><b>K7V</b>KESTREL SEVEN VOLT</span><span>Page No:04</span></div>
</section>

<!-- 05 Services -->
<section class="slide" style="left:19px;top:602px">
  <div class="slide-title">Our Services</div>
  <div class="brand-mark">K7V</div>
  <div class="card" style="left:16px;top:41px">
    <div class="photo" role="img" aria-label="House roof covered with solar panels" style="top:4px;background:linear-gradient(180deg,#2b4f82 0%,#a3563d 60%,#e6e0d6 100%)"></div>
    <div class="h9" style="top:104px">Solar Power for Homes</div>
    <ul style="top:125px"><li>Electricity Bill to go to Zero</li><li>Low Maintenance Cost</li><li>Assured Warranty upto 25 Years</li><li>Government Subsidies</li></ul>
  </div>
  <div class="card" style="left:173px;top:41px">
    <div class="h9" style="top:7px">Solar Power for Business</div>
    <ul style="top:37px"><li>Clean Energy</li><li>Tax Benefits</li><li>Grid Tied Systems</li><li>Finance Support</li></ul>
    <div class="photo" role="img" aria-label="Aerial view of factory rooftops fitted with solar panels" style="top:93px;background:linear-gradient(160deg,#c8d3db 0%,#486f92 50%,#a9b4bc 100%)"></div>
  </div>
  <div class="card" style="left:329px;top:41px">
    <div class="photo" role="img" aria-label="Utility scale solar power plant seen from above" style="top:4px;background:linear-gradient(180deg,#6c8f52 0%,#9aa9b7 35%,#3d5a7a 100%)"></div>
    <div class="h9" style="top:103px">Utility Scale Solar Power Plant</div>
    <ul style="top:125px"><li>Generate and Sell electricity to the government and industrial plants</li><li style="margin-top:5px">Long term stable prices for generated electricity from solar power plant</li></ul>
  </div>
  <div class="footer"><span class="name"><b>K7V</b>KESTREL SEVEN VOLT</span><span>Page No:05</span></div>
</section>

<!-- 06 Traction -->
<section class="slide" style="left:519px;top:602px">
  <div class="slide-title">Our Traction</div>
  <div class="brand-mark">K7V</div>
  <div class="chart-title">Company Name<br>Revenues</div>
  <svg class="abs" style="left:0;top:0" width="240" height="240" viewBox="0 0 240 240" font-family="Quicksand, sans-serif">
    <line x1="166" y1="76" x2="166" y2="219" stroke="#ddd" stroke-width=".8"/>
    <line x1="30" y1="219" x2="166" y2="219" stroke="#eee" stroke-width=".8"/>
    <rect x="33" y="90" width="24" height="129" fill="var(--orange)"/>
    <rect x="68" y="112" width="24" height="107" fill="var(--teal)"/>
    <rect x="101" y="154" width="24" height="65" fill="var(--magenta)"/>
    <g font-size="7" font-weight="600" fill="#111">
      <text x="35" y="87">₹ 9.47</text><text x="70" y="109">₹ 7.92</text><text x="103" y="151">₹ 4.08</text>
    </g>
    <g font-size="7" font-weight="600" fill="#111" text-anchor="start">
      <text x="171" y="84">₹ 0.00</text><text x="171" y="97">₹ 1.00</text><text x="171" y="109">₹ 2.00</text><text x="171" y="122">₹ 3.00</text><text x="171" y="134">₹ 4.00</text><text x="171" y="147">₹ 5.00</text><text x="171" y="160">₹ 6.00</text><text x="171" y="172">₹ 7.00</text><text x="171" y="185">₹ 8.00</text><text x="171" y="197">₹ 9.00</text><text x="169" y="210">₹ 10.00</text>
    </g>
    <g font-size="7" font-weight="600">
      <text transform="translate(19 118) rotate(-90)" fill="var(--orange)">2022-23</text>
      <rect x="13" y="120" width="4" height="4" fill="var(--orange)"/>
      <text transform="translate(19 165) rotate(-90)" fill="var(--teal)">2021-22</text>
      <rect x="13" y="168" width="4" height="4" fill="var(--teal)"/>
      <text transform="translate(19 211) rotate(-90)" fill="var(--magenta)">2020-21</text>
      <rect x="13" y="214" width="4" height="4" fill="var(--magenta)"/>
    </g>
    <text x="95" y="230" font-size="7" font-weight="600" text-anchor="middle" fill="#111">Revenues (in Cr.)</text>
  </svg>
  <div class="stat" style="left:248px;top:45px"><div class="num">8 MW</div><div class="lbl"><em>Total</em> Solar Capacity Installed</div><div class="desc">We have Installed 8 MW of Solar Panel Capacity for our clients, both industrial and residential</div></div>
  <div class="stat" style="left:360px;top:45px"><div class="num">132%</div><div class="lbl"><em>Topline</em> Growth</div><div class="desc" style="margin-top:14px">Our topline has grown by 132% in 2 years.</div></div>
  <div class="stat" style="left:248px;top:141px"><div class="num">2500+</div><div class="lbl"><em>Clients</em> Served</div><div class="desc" style="margin-top:8px">We have served 2500+ clients from diverse backgrounds</div></div>
  <div class="stat" style="left:360px;top:141px"><div class="num">16.8%</div><div class="lbl"><em>Gross</em> Margins</div><div class="desc" style="margin-top:8px">Scope for even higher gross margins with our own Manufacturing Plant.</div></div>
  <div class="footer"><span class="name"><b>K7V</b>KESTREL SEVEN VOLT</span><span>Page No:06</span></div>
</section>

<!-- 07 Roadmap -->
<section class="slide" style="left:19px;top:892px">
  <div class="slide-title">Growth Roadmap</div>
  <div class="brand-mark">K7V</div>
  <div class="photo" role="img" aria-label="Close-up of blue solar panels on green grass under a clear sky" style="left:19px;top:48px;width:168px;height:180px;border-radius:14px;background:linear-gradient(180deg,#3bb4e8 0%,#9ad6f0 28%,#1d3f9a 45%,#2a59c9 75%,#3f8a2d 100%)"></div>
  <svg class="abs" style="left:0;top:0" width="485" height="240"><line x1="245" y1="88" x2="245" y2="150" stroke="#bbb" stroke-width=".8" stroke-dasharray="2 2"/></svg>
  <div class="step-no" style="left:224px;top:46px"><span>01</span></div>
  <div class="step-no" style="left:224px;top:149px"><span>02</span></div>
  <div class="step" style="top:43px"><h3>First and Second<br>Year of Operations:</h3><ul><li>120MW of Solar Projects -₹480Cr</li><li>120MW of Solar Panel Sales - ₹240Cr</li><li>Target Revenue by 2nd Year - ₹720Cr</li></ul></div>
  <div class="step" style="top:146px"><h3>Second to Fourth<br>Year of Operations:</h3><ul><li>240MW of Solar Projects -₹960Cr</li><li>240MW of Solar Panel Sales - ₹480Cr</li><li>Target Revenue by 4th Year - ₹1440Cr</li></ul></div>
  <div class="footer"><span class="name"><b>K7V</b>KESTREL SEVEN VOLT</span><span>Page No:07</span></div>
</section>

<!-- 08 Appendix -->
<section class="slide" style="left:519px;top:892px">
  <div class="slide-title">Appendix</div>
  <div class="brand-mark">K7V</div>
  <div class="abs" style="left:0;width:485px;top:37px;text-align:center;font-size:14px;font-weight:600">Solar Panel Manufacturing Plant Layout</div>
  <div class="photo" role="img" aria-label="Technical floor plan drawing of the solar panel manufacturing plant" style="left:36px;top:59px;width:408px;height:164px;border:1px solid #ccc;background:linear-gradient(180deg,#fafafa 0%,#f0f2f3 100%)"></div>
  <div class="abs" style="left:0;width:457px;top:229px;text-align:center;font-size:7px;font-weight:500">Floor Plan</div>
  <div class="footer"><span class="name"><b>K7V</b>KESTREL SEVEN VOLT</span><span>Page No:08</span></div>
</section>

</div>
</body>
</html>
```